High-End Print/Digital Ad for Unique Luxury Travel Company Required

Objective:
Design a compelling and visually striking advertisement that highlights our company’s unmatched luxury travel experiences. The ad should elevate our brand image, spark curiosity, and drive prospective clients to contact us.
Target Audience:
• Affluent individuals seeking extraordinary, tailor-made travel experiences
• Affluent, luxury, high-net-worth individuals looking for value, expertise, and white-glove service
• Professionals or retirees who appreciate unique, thoughtfully curated travel over mainstream tourism
Key Messages to Communicate:
• One-of-a-kind luxury travel: Once-in-a-lifetime experiences that are curated with creativity and meticulous attention to detail
• Exceptional service: White-glove, personalized planning from start to finish
• 38 years’ travel experience – expert knowledge of destinations, modes of travel, premium accommodations and well-established, meaningful industry connections.
• Highly trusted: Cruise line executives often say, “No one does what you do.”
Tone and Style:
• Elegant, luxurious, sophisticated
• Eye-catching, polished, and modern
• Professional but warm—conveys trust and credibility
• High-impact visuals (full-bleed imagery, custom graphics, or high-end photography)
Deliverables:
• One full-page print ad and digital ad
• Ready-to-print, high-resolution file + working file (PSD, AI, etc.)
Optional: Social media-optimized version or short motion-graphic variation (if designer offers it)
Inspiration & Visual Style Suggestions:
• Think Lumen Voyages, Harrow Pike Wanderer, Silver Quill, or Orvel Retreats ad styles
• Large, emotive imagery with elegant typography
• Clean layout that speaks luxury, clarity, and trust
Copy Direction (draft):
For those who’ve explored the world—and crave something beyond the ordinary.
Each journey is a masterfully curated experience, rich in detail, seamless in execution, and unforgettable in every way.
Founded in 1997, Tidewell Journeys is a unique travel company specializing in cruising, all-inclusive luxury properties, and tours world-wide for individuals, groups, and incentives.
We offer an exceptional range of services designed to ensure every journey is flawlessly executed and truly unforgettable.
Let us help you plan your next extraordinary adventure.
Note: You may refine the copy slightly based on layout or format needs.
Other Resources for References:
1. Website - www.tidewelljourneys-example.com

```html
<!DOCTYPE html>
<html lang="en">
<head>
<meta charset="utf-8">
<title>Tidewell Journeys — One-of-a-kind Luxury Travel</title>
<link rel="stylesheet" href="https://fonts.googleapis.com/css2?family=Cinzel:wght@400;600;700&family=Lato:wght@400;700&display=swap">
<style>
  :root {
    --ink-white: #ffffff;
    --soft-white: #e9ece8;
    --gold: #d8b25a;
    --royal-blue: #1f3f96;
    --deep-red: #8e1b1b;
    --url-strip: #f3f1ec;
    --url-ink: #2a2a2a;
    --cave-dark: #0e1512;
    --cave-mid: #2f3a33;
    --cave-stone: #7d7a6c;
    --water-teal: #1f6b66;
  }
  * { box-sizing: border-box; margin: 0; padding: 0; }
  html, body { width: 774px; height: 1200px; overflow: hidden; background: #ffffff; }
  .ad {
    position: relative; width: 774px; height: 1200px; overflow: hidden;
    font-family: "Lato", Arial, sans-serif; color: var(--ink-white);
  }
  .ad__photo {
    position: absolute; inset: 0;
    background:
      radial-gradient(ellipse 42% 30% at 62% 22%, rgba(170,160,135,.55), transparent 70%),
      radial-gradient(ellipse 30% 25% at 30% 48%, rgba(125,122,108,.5), transparent 70%),
      radial-gradient(ellipse 60% 22% at 45% 88%, rgba(31,107,102,.85), transparent 75%),
      linear-gradient(180deg, var(--cave-dark) 0%, var(--cave-mid) 35%, #2a3530 60%, var(--water-teal) 85%, #12302c 100%);
  }
  .ad__shade {
    position: absolute; inset: 0;
    background: linear-gradient(180deg, rgba(0,0,0,.55) 0%, rgba(0,0,0,.15) 30%, rgba(0,0,0,.1) 60%, rgba(0,0,0,.55) 100%);
  }
  .headline {
    position: absolute; left: 44px; top: 58px; width: 690px;
    font-family: "Cinzel", Georgia, serif; font-weight: 700;
    font-size: 56px; line-height: 1.02; letter-spacing: .5px;
    text-shadow: 0 2px 8px rgba(0,0,0,.5);
  }
  .headline__big { font-size: 68px; }
  .tagline {
    position: absolute; left: 44px; top: 212px; width: 520px;
    font-size: 25px; line-height: 1.25; color: var(--soft-white);
    text-shadow: 0 1px 6px rgba(0,0,0,.6);
  }
  .features { position: absolute; left: 44px; top: 380px; width: 260px; }
  .feature { margin-bottom: 18px; }
  .feature__title {
    font-family: "Cinzel", Georgia, serif; font-weight: 600;
    font-size: 14px; color: var(--gold); letter-spacing: .5px; margin-bottom: 3px;
  }
  .feature__text { font-size: 11.5px; line-height: 1.35; color: var(--soft-white); }
  .promise {
    position: absolute; right: 22px; top: 568px; width: 372px;
    background: var(--royal-blue); padding: 22px 24px 24px; text-align: center;
  }
  .promise__title {
    font-family: "Cinzel", Georgia, serif; font-weight: 700;
    font-size: 23px; line-height: 1.12; margin-bottom: 12px;
  }
  .promise__text { font-size: 13px; line-height: 1.4; color: var(--soft-white); }
  .about { position: absolute; left: 380px; top: 850px; width: 360px; }
  .about__title {
    font-family: "Cinzel", Georgia, serif; font-weight: 700;
    font-size: 28px; color: var(--gold); margin-bottom: 10px;
  }
  .about__text { font-size: 13px; line-height: 1.42; color: var(--soft-white); margin-bottom: 10px; }
  .cta {
    position: absolute; left: 20px; right: 20px; top: 1106px; height: 36px;
    background: var(--deep-red); display: flex; align-items: center; justify-content: center;
    font-family: "Cinzel", Georgia, serif; font-weight: 700; font-size: 14px;
    letter-spacing: 1px; color: var(--gold); text-transform: uppercase;
  }
  .site {
    position: absolute; left: 0; right: 0; bottom: 0; height: 48px;
    background: var(--url-strip); color: var(--url-ink);
    display: flex; align-items: center; justify-content: center;
    font-family: "Cinzel", Georgia, serif; font-weight: 600; font-size: 17px; letter-spacing: 2px;
  }
</style>
</head>
<body>
<main class="ad">
  <div class="ad__photo" role="img" aria-label="Full-bleed photograph of a sunlit limestone cave opening onto still turquoise water"></div>
  <div class="ad__shade"></div>

  <h1 class="headline">One-of-a-kind<br><span class="headline__big">Luxury Travel</span></h1>
  <p class="tagline">Once-in-a-lifetime experiences that are curated with creativity and meticulous attention to detail.</p>

  <section class="features">
    <div class="feature">
      <h2 class="feature__title">Exceptional Service</h2>
      <p class="feature__text">White-glove, personalized planning from start to finish.</p>
    </div>
    <div class="feature">
      <h2 class="feature__title">38 Years' Travel Experience</h2>
      <p class="feature__text">Expert knowledge of destinations, modes of travel, premium accommodations and well-established, meaningful industry connections.</p>
    </div>
    <div class="feature">
      <h2 class="feature__title">Highly Trusted</h2>
      <p class="feature__text">Cruise line executives often say, “No one does what you do.”</p>
    </div>
  </section>

  <section class="promise">
    <h2 class="promise__title">For those who've explored the world and crave something beyond the ordinary.</h2>
    <p class="promise__text">Each journey is a masterfully curated experience, rich in detail, seamless in execution, and unforgettable in every way.</p>
  </section>

  <section class="about">
    <h2 class="about__title">Founded in 1997,</h2>
    <p class="about__text">Tidewell Journeys is a unique travel company specializing in cruising, all-inclusive luxury properties, and tours world-wide for individuals, groups, and incentives.</p>
    <p class="about__text">We offer an exceptional range of services designed to ensure every journey is flawlessly executed and truly unforgettable.</p>
  </section>

  <div class="cta">Let us help you plan your next extraordinary adventure.</div>
  <div class="site">www.tidewelljourneys-example.com</div>
</main>
</body>
</html>
```